Logistics Website Design

See website https://tqfreightglobal.com for theme and color details. Need the site to be re-done and reflect some of the designs shown in this list here: https://pixelvane.com/tags/logistics-company-website

Target Market(s)

Logistics & Transportation

Industry/Entity Type

Logistics and Supply Chain

Coding

Number of Pages Required

5+ page

Requirements
Must have
• Colors must match theme of logo. Looking for a sleek, interactive design.

```html
<!DOCTYPE html>
<html lang="en">
<head>
<meta charset="utf-8">
<title>TQ Freight Global — Delivering Strength in Every Mile</title>
<link rel="stylesheet" href="https://fonts.googleapis.com/css2?family=Archivo:wght@700;800;900&family=Inter:wght@400;500;600;700&display=swap">
<style>
:root{
  --ink:#1b1414;
  --page:#1c1717;
  --brown:#221615;
  --cream:#fbf0e8;
  --orange:#e8834f;
  --orange-text:#cf7a48;
  --ice:#e6f4fb;
  --white:#ffffff;
  --muted:#6b6360;
  --star:#f2a31b;
}
*{box-sizing:border-box;margin:0;padding:0}
html,body{width:1200px;height:2768px;overflow:hidden;background:var(--white)}
body{font-family:"Inter",sans-serif;color:var(--ink);position:relative}
.page{position:absolute;left:0;top:0;width:1200px;height:2387px;background:var(--page)}
.abs{position:absolute}
h1,h2,.display{font-family:"Archivo",sans-serif;font-weight:900;letter-spacing:-.5px}

/* hero */
.hero{left:13px;top:13px;width:1174px;height:636px;border-radius:22px;overflow:hidden;
  background:linear-gradient(100deg,#1a1614 0%,#2a2420 35%,#4a3a2a 60%,#8a6238 82%,#b07a40 100%)}
.hero-photo{position:absolute;inset:0;background:
  radial-gradient(ellipse 500px 260px at 920px 300px,rgba(214,150,80,.55),transparent 70%),
  linear-gradient(180deg,rgba(0,0,0,.1),rgba(0,0,0,.45))}
.brand{display:flex;align-items:center;gap:10px}
.brand-mark{width:34px;height:34px;border-radius:50%;background:var(--orange)}
.brand-name{font-family:"Inter",sans-serif;font-weight:700;font-size:17px;color:var(--white);letter-spacing:.5px}
.nav{left:75px;top:40px;width:1040px;display:flex;align-items:center}
.nav-links{display:flex;gap:0;margin-left:auto;align-items:center}
.nav-links a{color:var(--white);text-decoration:none;font-size:12px;font-weight:600;margin-left:38px}
.btn{display:inline-block;background:var(--orange);color:var(--ink);font-weight:700;text-decoration:none;border-radius:4px}
.nav .btn{margin-left:40px;padding:9px 18px;font-size:12px}
.hero h1{left:50px;top:238px;font-size:64px;line-height:58px;color:var(--white)}
.hero .lead{left:50px;top:384px;width:320px;font-size:16px;line-height:20px;color:var(--white)}
.hero .btn{left:50px;top:434px;padding:9px 25px;font-size:13px}

/* supply */
.supply{left:13px;top:663px;width:1174px;height:555px;border-radius:22px;background:var(--cream)}
.supply h2{left:37px;top:83px;font-size:31px;line-height:30px}
.supply .body{left:37px;top:195px;width:400px;font-size:13.5px;line-height:21px;color:#3a3230}
.map{left:551px;top:52px;width:586px;height:257px;border-radius:3px;
  background:radial-gradient(ellipse 300px 110px at 290px 120px,rgba(225,150,60,.45),transparent 70%),linear-gradient(180deg,#221c18,#171312)}
.card{background:var(--ice);border-radius:10px;box-shadow:0 4px 14px rgba(0,0,0,.05)}
.support{left:37px;top:398px;width:263px;height:75px;display:flex;align-items:center;padding:0 14px;gap:12px}
.avatar{width:31px;height:31px;border-radius:50%;display:flex;align-items:center;justify-content:center;font-size:14px;flex:none}
.av-su{background:#bfe0f5;color:#1b1414}
.support b{font-size:9.5px;display:block}
.support small{font-size:8px;color:var(--muted);display:block;margin:4px 0}
.pill{display:inline-block;background:var(--orange);color:var(--ink);font-size:7.5px;font-weight:700;padding:2px 7px;border-radius:3px}
.faith{left:320px;top:393px;width:540px;text-align:center}
.eyebrow{font-size:9px;color:var(--orange);letter-spacing:1px;font-weight:500}
.faith h3{font-family:"Archivo",sans-serif;font-weight:800;font-size:19px;line-height:20px;margin-top:10px}
.users{display:flex;justify-content:center;align-items:center;gap:4px;margin-top:8px;font-size:9px;color:var(--orange);font-weight:600}
.dot{width:18px;height:18px;border-radius:50%;font-size:8px;display:flex;align-items:center;justify-content:center;color:var(--ink)}
.booking{left:874px;top:365px;width:263px;height:141px;padding:14px 13px;font-size:9px}
.booking .row{display:flex;justify-content:space-between;margin-top:19px}
.booking hr{border:0;border-top:1px solid #c9d5dc;margin:16px 0 0}

/* services */
.services{left:13px;top:1237px;width:1174px;height:535px;border-radius:22px;background:var(--brown)}
.services h2{left:37px;top:69px;font-size:31px;color:var(--cream)}
.services h4{left:37px;top:158px;font-family:"Inter",sans-serif;font-weight:600;font-size:26px;color:var(--orange-text)}
.services .desc{left:37px;top:224px;width:380px;font-size:16px;line-height:18px;color:var(--cream)}
.services .desc p+p{margin-top:18px}
.services .btn{left:37px;top:364px;padding:6px 20px;font-size:11px}
.tile{width:280px;height:218px;border-radius:10px;overflow:hidden;color:var(--white)}
.tile.active{outline:2px solid #f3c9a6}
.tile-photo{position:absolute;inset:0}
.tile-shade{position:absolute;inset:0;background:linear-gradient(180deg,transparent 45%,rgba(20,14,12,.8))}
.tile b{position:absolute;left:13px;bottom:33px;font-family:"Archivo",sans-serif;font-weight:800;font-size:12.5px}
.tile small{position:absolute;left:13px;bottom:14px;font-size:8.5px;opacity:.85}

/* testimonials */
.testi{left:13px;top:1791px;width:1174px;height:275px;border-radius:22px;background:var(--cream)}
.testi h2{left:25px;top:47px;font-size:28px}
.arrows{right:25px;top:46px;display:flex;gap:6px}
.arrows span{width:25px;height:25px;border-radius:50%;border:1px solid var(--ink)}
.quote{top:103px;width:362px;height:135px;background:var(--white);border-radius:8px;padding:20px 18px;font-size:10px}
.quote .top{display:flex;justify-content:space-between;font-size:8.5px;color:var(--muted)}
.quote .top em{font-style:normal;color:var(--star);font-weight:600}
.quote p{margin-top:15px;line-height:15px}
.who{display:flex;align-items:center;gap:10px;margin-top:12px}
.who b{font-size:9.5px;display:block}
.who small{font-size:8.5px;color:var(--muted)}

/* footer */
.footer{left:13px;top:2084px;width:1174px;height:290px;color:var(--cream)}
.footer .brand{left:67px;top:45px}
.connect{left:440px;top:40px;width:140px;text-align:right;font-size:9.5px;line-height:18px}
.connect h5{font-family:"Archivo",sans-serif;font-size:13px;margin-bottom:4px}
.signup{left:37px;top:154px;font-size:20px;line-height:20px}
.form{left:37px;top:200px;display:flex;gap:9px}
.field{width:219px;height:26px;border:1px solid #3a2e2c;border-radius:3px;background:#201716;font-size:8.5px;color:#8b7f7a;padding:8px 12px}
.form .btn{padding:6px 14px;font-size:11px}
.foot-links{right:37px;top:63px;text-align:right;font-family:"Archivo",sans-serif;font-weight:800;font-size:11px;line-height:30px}
.copy{right:37px;top:230px;font-size:8.5px;color:#b8aaa4}
</style>
</head>
<body>
<div class="page">

  <section class="hero abs">
    <div class="hero-photo" role="img" aria-label="Row of parked freight trucks at a depot under a sunset sky"></div>
    <nav class="nav abs">
      <div class="brand"><span class="brand-mark"></span><span class="brand-name">TQ FREIGHT</span></div>
      <div class="nav-links">
        <a href="#">Home</a><a href="#">Services</a><a href="#">Industries</a><a href="#">Request a Quote</a><a href="#">About Us</a><a href="#">Contact Us</a>
        <a class="btn" href="#">Get Quote</a>
      </div>
    </nav>
    <h1 class="abs">DELIVERING STRENGTH<br>IN EVERY MILE</h1>
    <p class="lead abs">Secure and reliable transportation for all your cargo needs.</p>
    <a class="btn abs" href="#">REQUEST A QUOTE</a>
  </section>

  <section class="supply abs">
    <h2 class="abs">KEEPING YOUR SUPPLY CHAIN<br>MOVING</h2>
    <p class="body abs">We deliver a comprehensive range of open- deck and specialized transportation services. Backed by years of experience, a trusted nationwide carrier network, and a strong safety-first culture.</p>
    <div class="map abs" role="img" aria-label="Dark world map with glowing global trade routes and network statistics"></div>

    <div class="support card abs">
      <span class="avatar av-su">SU</span>
      <div><b>Customer Support</b><small>Hello! How can I help you?</small><span class="pill">Contact Support</span></div>
    </div>

    <div class="faith abs">
      <div class="eyebrow">COMPREHENSIVE</div>
      <h3>DELIVERING FAITH, PEACE OF MIND, AND UNPARALLELED QUALITY</h3>
      <div class="users"><span class="dot" style="background:#8fcf5a">A</span><span class="dot" style="background:#c9c4c0">B</span><span style="margin-left:14px">20K+ Monthly Users</span></div>
    </div>

    <div class="booking card abs">
      <b>TOTAL BOOKING</b>
      <div class="row"><span>Steel Core Shipment</span><b>$650,200</b></div>
      <div class="row"><span>Medicine Shipment</span><b>$825.40</b></div>
      <hr>
      <div class="row" style="margin-top:10px"><b>Total Shipments</b><span style="color:var(--orange)">320,200</span></div>
    </div>
  </section>

  <section class="services abs">
    <h2 class="abs">OUR SERVICES</h2>
    <h4 class="abs">Step Deck Transportation</h4>
    <div class="desc abs">
      <p>Our step deck trucking services support tall, heavy, and specialized freight that requires additional height clearance and flexible loading options.</p>
      <p>Service description here changes depending on what the user is hovering over.</p>
    </div>
    <a class="btn abs" href="#">Request a Quote →</a>

    <div class="tile abs" style="left:564px;top:41px">
      <div class="tile-photo" role="img" aria-label="Blue semi truck hauling a flatbed load at dusk" style="background:linear-gradient(180deg,#5e6d7c,#2d3744 60%,#1e2228)"></div>
      <div class="tile-shade"></div><b>FLATBED TRANSPORTATION</b><small>Routine shipments to heavy-haul loads</small>
    </div>
    <div class="tile abs" style="left:857px;top:41px">
      <div class="tile-photo" role="img" aria-label="Port crane lifting a blue shipping container over a harbor" style="background:linear-gradient(180deg,#8fa8c0,#4b6a8a 50%,#3a3e44)"></div>
      <div class="tile-shade"></div><b>HEAVY HAUL TRANSPORTATION</b><small>Oversized, overweight, &amp; over-dimensional freight</small>
    </div>
    <div class="tile abs active" style="left:564px;top:271px">
      <div class="tile-photo" role="img" aria-label="Semi truck with a step deck trailer at sunset" style="background:linear-gradient(180deg,#c9a77a,#6a5a4e 45%,#2f2a28)"></div>
      <div class="tile-shade"></div><b>STEP DECK TRANSPORTATION</b><small>Routine shipments to heavy-haul loads</small>
    </div>
    <div class="tile abs" style="left:857px;top:271px">
      <div class="tile-photo" role="img" aria-label="White dry van truck at a warehouse loading dock" style="background:linear-gradient(180deg,#b8bcc0,#8a8d90 50%,#4a4c4e)"></div>
      <div class="tile-shade"></div><b>DRY VAN TRANSPORTATION</b><small>Oversized, overweight, &amp; over-dimensional freight</small>
    </div>
  </section>

  <section class="testi abs">
    <h2 class="abs">OUR CLIENT TESTIMONIALS</h2>
    <div class="arrows abs"><span></span><span></span></div>

    <article class="quote abs" style="left:25px">
      <div class="top"><span>CLIENT:</span><em>4.8 ☆</em></div>
      <p>"Top-notch logistics with expert, and dedicated support for all your cargo transport needs."</p>
      <div class="who"><span class="avatar" style="background:#d81b1b">OC</span><div><b>Owen Calder</b><small>General Manager</small></div></div>
    </article>
    <article class="quote abs" style="left:406px">
      <div class="top"><span>CLIENT:</span><em>4.7 ☆</em></div>
      <p>"We trust your dedicated team and we highly recommend them as a leading freight forwarder."</p>
      <div class="who"><span class="avatar" style="background:#1698a8;color:#fff">RO</span><div><b>Rafael Oduya</b><small>Business Proprietor</small></div></div>
    </article>
    <article class="quote abs" style="left:787px">
      <div class="top"><span>CLIENT:</span><em>5.0 ☆</em></div>
      <p>"Exceptional 24/7 logistics support as a professional, fully committed team just to solve your headache."</p>
      <div class="who"><span class="avatar" style="background:#12a8f0">LM</span><div><b>Lena Marwick</b><small>Business Director</small></div></div>
    </article>
  </section>

  <footer class="footer abs">
    <div class="brand abs"><span class="brand-mark"></span><span class="brand-name">TQ FREIGHT</span></div>
    <div class="connect abs">
      <h5>CONNECT WITH US</h5>
      <div>☏ +1 (800) 555-0142</div>
      <div>✉ info@tqfreight.com</div>
    </div>
    <div class="signup display abs">SIGN UP<br>TO STAY UPTO DATE</div>
    <form class="form abs">
      <div class="field">Your Name</div>
      <div class="field">Email Address</div>
      <a class="btn" href="#">Submit →</a>
    </form>
    <div class="foot-links abs">
      <div>SERVICES</div><div>CONTACT US</div><div>TRACKING</div><div>ABOUT US</div><div>PRIVACY POLICY</div>
    </div>
    <div class="copy abs">© 2026. An independent agent of Bram Holt LLC.</div>
  </footer>

</div>
</body>
</html>
```